To design a brand identity that is simple and creative with 'Corvane' as the brand name, I like modern simple fonts like helvetica neue, I want to print both sides of the card, I am open to dark front and white back, but the design needs to transfer well to letter heads and email signatures, I am looking for sophisticated and elegant, but open minded about clever and off the wall, I do not do 'boring' Corvane Ventures is the mother company for a small group, specialising in Management & consulting, Software development and construction, we have a high level of integrity, we are transparent and accountable for what we do. my images are provided as a guide only, Im not expecting them to be just copied, Im looking for a creator and passionate thinker, who will put life into their work.

Target Market(s)

usually business minded people who are looking for something different in me, such as leadership, confidence and focus with thinking that is per haps a little outside the box..

Industry/Entity Type

Construction

Requirements
Must have
• clean, minmalistic
Nice to have
• custom logo
Should not have
• boring, traditional

```html
<!DOCTYPE html>
<html lang="en">
<head>
<meta charset="UTF-8">
<title>Corvane Business Card</title>
<link href="https://fonts.googleapis.com/css2?family=Open+Sans:wght@300;400;600;700&display=swap" rel="stylesheet">
<style>
  :root {
    --stage: #ecebe8;
    --ink-dark: #1c1c1e;
    --ink-dark-2: #2b2b2e;
    --orange: #f06a2a;
    --amber: #f7a21b;
    --magenta: #a3226e;
    --teal: #1aa39a;
    --white: #ffffff;
    --text-grey: #4a4a4a;
    --text-light: #e9e9e9;
  }
  * { box-sizing: border-box; margin: 0; padding: 0; }
  html, body { width: 1200px; height: 720px; overflow: hidden; }
  body {
    background: var(--stage);
    font-family: "Open Sans", "Helvetica Neue", Arial, sans-serif;
    position: relative;
  }
  .card {
    position: absolute;
    width: 560px;
    height: 320px;
    border-radius: 4px;
    overflow: hidden;
    box-shadow: 0 10px 30px rgba(0,0,0,0.18);
  }

  /* Front: dark side */
  .card--front { left: 50px; top: 60px; color: var(--text-light); }
  .front__texture {
    position: absolute; inset: 0;
    background: linear-gradient(135deg, var(--ink-dark-2) 0%, var(--ink-dark) 100%);
  }
  .brand {
    position: absolute;
    display: flex;
    align-items: center;
    gap: 18px;
  }
  .brand__dot {
    width: 56px; height: 56px; border-radius: 50%;
    background: var(--orange);
    flex: none;
  }
  .brand__name {
    font-weight: 300;
    color: var(--orange);
    line-height: 1;
    letter-spacing: 1px;
  }
  .card--front .brand { left: 48px; top: 52px; }
  .card--front .brand__name { font-size: 78px; }

  .contact { position: absolute; left: 48px; top: 178px; }
  .contact__person { font-size: 17px; font-weight: 700; color: var(--orange); margin-bottom: 14px; }
  .contact__title { font-weight: 400; color: var(--white); }
  .contact__line {
    display: flex; align-items: center; gap: 9px;
    font-size: 13px; margin-bottom: 8px; color: var(--text-light);
  }
  .contact__icon { width: 14px; height: 14px; flex: none; }

  .front__bands { position: absolute; left: 0; bottom: 0; width: 560px; height: 60px; }
  .front__address {
    position: absolute; right: 24px; bottom: 26px;
    font-size: 12px; color: var(--white); font-weight: 600;
  }

  /* Back: white side */
  .card--back { left: 590px; top: 340px; background: var(--white); }
  .card--back .brand { left: 86px; top: 70px; }
  .card--back .brand__dot { width: 64px; height: 64px; }
  .card--back .brand__name { font-size: 86px; }
  .back__services {
    position: absolute; left: 0; right: 0; top: 196px;
    text-align: center; font-size: 21px; color: var(--text-grey);
  }
  .back__web {
    position: absolute; left: 0; right: 0; top: 240px;
    text-align: center; font-size: 17px; letter-spacing: 4px; color: var(--text-grey);
  }
</style>
</head>
<body>

<section class="card card--front">
  <div class="front__texture" role="img" aria-label="Dark charcoal surface with fine diagonal pinstripe texture"></div>

  <div class="brand">
    <span class="brand__dot"></span>
    <span class="brand__name">corvane</span>
  </div>

  <div class="contact">
    <p class="contact__person">Your Name, <span class="contact__title">Title</span></p>
    <p class="contact__line">
      <svg class="contact__icon" viewBox="0 0 14 14"><circle cx="7" cy="7" r="7" fill="#f06a2a"/><path d="M4.6 3.6l1.3 1.6-.7.9c.5 1 1.2 1.7 2.2 2.2l.9-.7 1.6 1.3-.8 1.2C6.4 9.8 4.2 7.6 3.9 4.4z" fill="#fff"/></svg>
      +61 0400 555 217
    </p>
    <p class="contact__line">
      <svg class="contact__icon" viewBox="0 0 14 14"><circle cx="7" cy="7" r="7" fill="#a3226e"/><rect x="3.5" y="4.6" width="7" height="5" fill="none" stroke="#fff" stroke-width="1"/><path d="M3.5 4.6L7 7.4l3.5-2.8" fill="none" stroke="#fff" stroke-width="1"/></svg>
      Names@corvane.ventures
    </p>
  </div>

  <svg class="front__bands" viewBox="0 0 560 60" preserveAspectRatio="none">
    <defs>
      <linearGradient id="address-band" x1="0" x2="1" y1="0" y2="0">
        <stop offset="0" stop-color="#f06a2a"/>
        <stop offset="0.35" stop-color="#f7a21b"/>
        <stop offset="0.7" stop-color="#a3226e"/>
        <stop offset="1" stop-color="#1aa39a"/>
      </linearGradient>
    </defs>
    <polygon points="318,12 560,12 560,44 300,44" fill="url(#address-band)"/>
    <rect x="0" y="44" width="560" height="16" fill="#f06a2a"/>
  </svg>
  <p class="front__address">Po Box 512 Halden 6090</p>
</section>

<section class="card card--back">
  <div class="brand">
    <span class="brand__dot"></span>
    <span class="brand__name">corvane</span>
  </div>
  <p class="back__services">Management • Software • Construction</p>
  <p class="back__web">www.corvane.com</p>
</section>

</body>
</html>
```